Business Card Design for Marketing Firm

Looking for business card design for higher end marketing firm. Clean but impressionable/trendy. We are a marketing firm that represents manufacturers in the foodservice equipment and supply industry. Our customers are end users such has hotels, restaurants, country clubs, convention centers and casinos as well as distributors of restaurants supplies and equipment, and manufacturers of foodservice equipment and supplies.
Target Market(s)
Hotels, Restaurants, Supply & Equipment Distributors, Foodservice Manufacturers
Industry/Entity Type
Foodservice/Hospitality
Contact Information for Business Card
Name, Title, Contact Number, Email, Website, Social Media, Address
Requirements
Must have
- Clean & Simple but Serious and Impressionable

```html
<!DOCTYPE html>
<html lang="en">
<head>
<meta charset="utf-8">
<title>Meridian Hospitality Reps — Business Card</title>
<link rel="stylesheet" href="https://fonts.googleapis.com/css2?family=Marcellus&family=Montserrat:wght@400;700&display=swap">
<style>
  :root {
    --navy: #1b1878;
    --paper: #ececec;
    --backdrop: #676767;
    --ink: #1a1a1a;
  }
  html, body {
    margin: 0;
    width: 1200px;
    height: 1047px;
    overflow: hidden;
    background: var(--backdrop);
  }
  .card {
    position: absolute;
    box-sizing: border-box;
    border-radius: 3px;
    box-shadow: 0 10px 28px rgba(0,0,0,.28);
  }
  /* Front: portrait, white */
  .card-front {
    left: 90px;
    top: 226px;
    width: 340px;
    height: 595px;
    background: var(--paper);
    color: var(--navy);
    display: flex;
    flex-direction: column;
    align-items: center;
    padding: 62px 34px 40px;
  }
  .wordmark {
    font-family: "Marcellus", serif;
    font-size: 25px;
    line-height: 1.25;
    letter-spacing: 1px;
    text-align: center;
    color: var(--navy);
    margin: 0;
  }
  .wordmark-front { margin-top: 70px; }
  .person {
    margin-top: 64px;
    text-align: center;
  }
  .person-name {
    font-family: "Montserrat", sans-serif;
    font-weight: 700;
    font-size: 17px;
    letter-spacing: .5px;
    margin: 0;
  }
  .person-title {
    font-family: "Montserrat", sans-serif;
    font-weight: 400;
    font-size: 14px;
    color: var(--ink);
    margin: 3px 0 0;
  }
  .icon-row {
    display: flex;
    align-items: center;
    gap: 6px;
    margin-top: 16px;
    width: 100%;
  }
  .icon-row .rule {
    flex: 1;
    height: 1.5px;
    background: var(--navy);
  }
  .icon {
    width: 22px;
    height: 22px;
    display: block;
  }
  .contact {
    margin-top: 14px;
    font-family: "Montserrat", sans-serif;
    font-size: 14px;
    line-height: 1.45;
    color: var(--ink);
    text-align: center;
  }
  .contact p { margin: 0; }
  .divider {
    width: 70%;
    height: 1.5px;
    background: var(--navy);
    margin: 14px 0;
  }
  /* Back: landscape, navy */
  .card-back {
    left: 500px;
    top: 353px;
    width: 595px;
    height: 340px;
    background: var(--navy);
    display: flex;
    align-items: center;
    justify-content: center;
  }
  .wordmark-back {
    color: var(--paper);
    font-size: 36px;
  }
</style>
</head>
<body>
  <section class="card card-front" aria-label="Business card front">
    <p class="wordmark wordmark-front">MERIDIAN<br>HOSPITALITY<br>REPS</p>

    <div class="person">
      <p class="person-name">DANIEL HALE</p>
      <p class="person-title">Managing Director</p>
    </div>

    <div class="icon-row">
      <span class="rule"></span>
      <svg class="icon" viewBox="0 0 22 22" aria-label="Phone">
        <rect width="22" height="22" rx="4" fill="var(--navy)"/>
        <path d="M7 5.5c.8-.4 1.5 0 1.9.9l.7 1.6c.3.7 0 1.3-.5 1.7l-.6.4c.6 1.4 1.6 2.4 3 3l.4-.6c.4-.5 1-.8 1.7-.5l1.6.7c.9.4 1.3 1.1.9 1.9-.6 1.2-1.8 1.9-3.2 1.5-3.4-1-6-3.6-7-7-.4-1.4.3-2.6 1.1-3.6z" fill="var(--paper)"/>
      </svg>
      <svg class="icon" viewBox="0 0 22 22" aria-label="Email">
        <rect width="22" height="22" rx="4" fill="var(--navy)"/>
        <rect x="5" y="7" width="12" height="9" rx="1" fill="none" stroke="var(--paper)" stroke-width="1.5"/>
        <path d="M5.5 7.5 11 12l5.5-4.5" fill="none" stroke="var(--paper)" stroke-width="1.5"/>
      </svg>
      <svg class="icon" viewBox="0 0 22 22" aria-label="Website">
        <rect width="22" height="22" rx="4" fill="var(--navy)"/>
        <circle cx="11" cy="11" r="6" fill="none" stroke="var(--paper)" stroke-width="1.4"/>
        <ellipse cx="11" cy="11" rx="2.6" ry="6" fill="none" stroke="var(--paper)" stroke-width="1.2"/>
        <path d="M5 11h12" stroke="var(--paper)" stroke-width="1.2"/>
      </svg>
      <span class="rule"></span>
    </div>

    <div class="contact">
      <p>555 014 2290</p>
      <p>info@meridianreps.com</p>
      <p>www.meridianreps.com</p>
    </div>
    <div class="divider"></div>
    <div class="contact" style="margin-top:0">
      <p>1180 Harbor View Drive</p>
      <p>Seacliff CA 92651</p>
    </div>
  </section>

  <section class="card card-back" aria-label="Business card back">
    <p class="wordmark wordmark-back">MERIDIAN HOSPITALITY<br>REPS</p>
  </section>
</body>
</html>
```